label design for soy candle

I am a start up making soy candles and other products involving scents.
On the label should be in writing : the scent, Handgemacht in der Schweiz, Sojakerze, my logo with the name Pellwick Candles on it. I will upload the currant label of my candles, but I want something more fashioned. The color of the label should be black with the scent written in gold, and the rest in white. Or maybe suggest something different, I am open to new designs. I am also open to change the logo, except the flower has to stay.
Sizes : square 60x60mm / round 50mm / rectangle 70x20mm ( for different jars )

```html
<!DOCTYPE html>
<html lang="de">
<head>
<meta charset="utf-8">
<title>Pellwick Candles – Citrus Basil Sojakerze Etikett</title>
<link rel="stylesheet" href="https://fonts.googleapis.com/css2?family=Bodoni+Moda:opsz,wght@6..96,500&family=Jost:wght@400;500&display=swap">
<style>
  :root {
    --page-bg: #ffffff;
    --label-black: #0b0c0e;
    --text-white: #ffffff;
    --gold-light: #e9c46f;
    --gold-mid: #c99a3e;
    --gold-deep: #8e6420;
  }
  html, body {
    margin: 0;
    padding: 0;
    width: 1200px;
    height: 1200px;
    overflow: hidden;
    background: var(--page-bg);
  }
  .canvas {
    position: relative;
    width: 1200px;
    height: 1200px;
    background: var(--page-bg);
  }
  .label {
    position: absolute;
    left: 150px;
    top: 150px;
    width: 900px;
    height: 900px;
    background: var(--label-black);
    color: var(--text-white);
    font-family: "Jost", sans-serif;
    text-align: center;
  }
  .brand-name {
    position: absolute;
    left: 0;
    right: 0;
    top: 178px;
    margin: 0;
    font-size: 28px;
    font-weight: 500;
    letter-spacing: 0.08em;
    text-transform: uppercase;
    color: var(--text-white);
  }
  .brand-mark {
    position: absolute;
    left: 50%;
    top: 110px;
    width: 44px;
    height: 44px;
    margin-left: -22px;
    border-radius: 50%;
    background: var(--text-white);
  }
  .scent-name {
    position: absolute;
    left: 0;
    right: 0;
    top: 340px;
    margin: 0;
    font-family: "Bodoni Moda", serif;
    font-weight: 500;
    font-size: 138px;
    line-height: 1;
    letter-spacing: -0.01em;
    background: linear-gradient(100deg, var(--gold-deep) 0%, var(--gold-light) 30%, var(--gold-mid) 55%, var(--gold-light) 78%, var(--gold-deep) 100%);
    -webkit-background-clip: text;
    background-clip: text;
    color: transparent;
  }
  .product-type {
    position: absolute;
    left: 0;
    right: 0;
    top: 685px;
    margin: 0;
    font-size: 42px;
    font-weight: 400;
    letter-spacing: 0.12em;
    text-transform: uppercase;
  }
  .gold-divider {
    position: absolute;
    left: 50%;
    top: 756px;
    width: 72px;
    height: 3px;
    margin-left: -36px;
    background: linear-gradient(90deg, var(--gold-deep), var(--gold-light), var(--gold-deep));
  }
  .origin {
    position: absolute;
    left: 0;
    right: 0;
    top: 793px;
    margin: 0;
    padding-left: 0.62em;
    font-size: 24px;
    font-weight: 500;
    letter-spacing: 0.62em;
    text-transform: uppercase;
  }
</style>
</head>
<body>
  <main class="canvas">
    <section class="label" aria-label="Etikett Sojakerze Citrus Basil">
      <span class="brand-mark" aria-hidden="true"></span>
      <p class="brand-name">Pellwick Candles</p>
      <h1 class="scent-name">Citrus Basil</h1>
      <p class="product-type">Sojakerze</p>
      <span class="gold-divider" aria-hidden="true"></span>
      <p class="origin">Handgemacht in der Schweiz</p>
    </section>
  </main>
</body>
</html>
```